Medical VIP club - small design

Please read the specs in a design brief attached. Also we don't have logo in a Vector format and attaching the only version we have.

Club

```html
<!DOCTYPE html>
<html lang="en">
<head>
<meta charset="utf-8">
<title>Veloria — VIP Club</title>
<link href="https://fonts.googleapis.com/css2?family=Arimo:wght@400;700&family=Carlito:wght@400;700&display=swap" rel="stylesheet">
<style>
:root{
  --header-top:#8c7c66;
  --header-bottom:#6f604c;
  --body-brown:#6b5b47;
  --tab-light:#e9dfcd;
  --tab-mid:#b5a386;
  --tab-dark:#8d7a5d;
  --tab-active-top:#e8cf4a;
  --tab-active-bottom:#b8960f;
  --band-cream:#efe6d3;
  --logo-brown:#5a4632;
  --frame-light:#d9cdb6;
  --arrow-gold:#f2c531;
  --text-white:#ffffff;
  --footer-top:#f4ede0;
  --footer-bottom:#d6c9b1;
  --footer-text:#3b3024;
}
*{margin:0;padding:0;box-sizing:border-box}
html,body{width:1200px;height:1046px;overflow:hidden;background:var(--body-brown)}
.page{position:relative;width:1200px;height:1046px;font-family:"Arimo",Arial,sans-serif;overflow:hidden}

.site-header{position:absolute;left:0;top:0;width:1200px;height:279px;
  background:linear-gradient(180deg,var(--header-top),var(--header-bottom))}
.brand{position:absolute;left:40px;top:78px;display:flex;align-items:center;gap:14px}
.brand-mark{width:34px;height:34px;border-radius:50%;background:var(--logo-brown)}
.brand-name{font-weight:700;font-size:56px;color:var(--logo-brown);letter-spacing:-1px;line-height:1}

.hotline{position:absolute;left:790px;top:52px;display:flex;align-items:center;gap:22px}
.hotline-icon{width:104px;height:104px}
.hotline-number{font-weight:700;font-size:45px;color:var(--text-white);
  text-shadow:0 2px 3px rgba(40,28,15,.8)}

.nav-band{position:absolute;left:0;top:242px;width:1200px;height:37px;
  background:linear-gradient(180deg,var(--band-cream),#cdbf9f)}
.main-nav{position:absolute;left:24px;top:207px;display:flex;gap:3.6px}
.main-nav a{display:flex;align-items:center;justify-content:center;width:190px;height:72px;
  border-radius:14px 14px 0 0;color:var(--text-white);text-decoration:none;font-size:20px;
  padding-top:10px;
  background:linear-gradient(180deg,var(--tab-light) 0%,var(--tab-mid) 45%,var(--tab-dark) 100%);
  box-shadow:inset 0 1px 0 rgba(255,255,255,.6);text-shadow:0 1px 2px rgba(60,45,25,.6)}
.main-nav a.is-active{background:linear-gradient(180deg,var(--tab-active-top),var(--tab-active-bottom))}

.content{position:absolute;left:0;top:279px;width:1200px;height:674px;background:var(--body-brown)}
.hero{position:absolute;left:24px;top:11px;width:1158px;height:420px;border:2px solid var(--frame-light);
  background:linear-gradient(90deg,#8a6a3a 0%,#c9a877 25%,#b39a7c 50%,#c9a877 75%,#7d5f35 100%)}
.hero-photo{position:absolute;inset:0;
  background:radial-gradient(ellipse at 50% 30%,rgba(255,226,160,.55),transparent 60%),
             linear-gradient(180deg,rgba(0,0,0,0) 60%,rgba(60,40,20,.5))}
.hero-title{position:absolute;left:682px;top:210px;font-family:"Carlito","Calibri",sans-serif;
  font-size:94px;color:#e6e1d8;line-height:1;text-shadow:0 2px 4px rgba(30,20,10,.9)}
.hero-text{position:absolute;left:708px;top:324px;width:380px;font-weight:700;font-size:20px;
  line-height:26px;color:var(--text-white);text-shadow:0 1px 3px rgba(0,0,0,.8)}
.hero-arrow{position:absolute;top:188px;width:56px;height:68px}
.hero-arrow.prev{left:18px}
.hero-arrow.next{right:18px}

.tiles{position:absolute;left:24px;top:441px;display:flex;gap:10.5px}
.tile{width:223px;height:202px;border:2px solid var(--frame-light)}
.tile.hospital{background:linear-gradient(135deg,#c7ddf0,#6b9bd0 60%,#d23b3b)}
.tile.travel{background:linear-gradient(135deg,#1f5fd1,#3b8ef0 55%,#1a4fb3)}
.tile.resort{background:linear-gradient(180deg,#8cc8ec,#e8f2f5 50%,#7ca36a)}
.tile.doctors{background:linear-gradient(180deg,#f5f6f8,#dfe5ec)}
.tile.membership{background:linear-gradient(135deg,#eef3f7,#b7cad8)}

.site-footer{position:absolute;left:0;top:953px;width:1200px;height:93px;
  background:linear-gradient(180deg,var(--footer-top),var(--footer-bottom));border-top:2px solid #a8967a}
.social{position:absolute;left:24px;top:29px;display:flex;gap:6px}
.social span{width:37px;height:37px;border-radius:6px;background:#8a7659;box-shadow:0 1px 2px rgba(0,0,0,.3)}
.copyright{position:absolute;left:0;width:1200px;top:47px;text-align:center;font-size:13px;color:var(--footer-text);padding-right:60px}
.footer-brand{position:absolute;right:24px;top:26px;display:flex;align-items:center;gap:8px}
.footer-brand .brand-mark{width:22px;height:22px}
.footer-brand .brand-name{font-size:36px}
</style>
</head>
<body>
<div class="page">
  <header class="site-header">
    <div class="brand"><span class="brand-mark"></span><span class="brand-name">Veloria</span></div>
    <div class="hotline">
      <svg class="hotline-icon" viewBox="0 0 104 104" aria-hidden="true">
        <defs>
          <radialGradient id="hotlineGlow" cx="50%" cy="35%" r="65%">
            <stop offset="0" stop-color="#f3d7a0"/>
            <stop offset=".6" stop-color="#a9782f"/>
            <stop offset="1" stop-color="#5e3f16"/>
          </radialGradient>
        </defs>
        <circle cx="52" cy="52" r="50" fill="url(#hotlineGlow)" stroke="#4e3a22" stroke-width="2"/>
        <path d="M24 44c0-8 12-12 28-12s28 4 28 12v4h-12v-6c-4-2-10-3-16-3s-12 1-16 3v6H24z" fill="#fff"/>
        <path d="M34 52h36l6 22H28z" fill="#fff"/>
        <circle cx="52" cy="63" r="6" fill="#a9782f"/>
      </svg>
      <span class="hotline-number">416-555-010</span>
    </div>
  </header>

  <div class="nav-band"></div>
  <nav class="main-nav">
    <a href="#">About Us</a>
    <a href="#">VIP Club</a>
    <a href="#">Services</a>
    <a href="#">Packages &amp; Prices</a>
    <a href="#" class="is-active">Registration</a>
    <a href="#">Contacts</a>
  </nav>

  <main class="content">
    <section class="hero">
      <div class="hero-photo" role="img" aria-label="Grand palace hall with gilded chandeliers and marble columns"></div>
      <svg class="hero-arrow prev" viewBox="0 0 56 68" aria-hidden="true"><path d="M40 2L4 34l36 32h14L20 34 54 2z" fill="var(--arrow-gold)"/></svg>
      <svg class="hero-arrow next" viewBox="0 0 56 68" aria-hidden="true"><path d="M16 2l36 32-36 32H2l34-32L2 2z" fill="var(--arrow-gold)"/></svg>
      <h1 class="hero-title">VIP Club</h1>
      <p class="hero-text">Lorem ipsum dolor. Lorem ipsum dolor. Lorem ipsum dolor...</p>
    </section>

    <div class="tiles">
      <div class="tile hospital" role="img" aria-label="Hospital building with emergency sign"></div>
      <div class="tile travel" role="img" aria-label="Airplanes flying over a blue world map"></div>
      <div class="tile resort" role="img" aria-label="Couple on a seaside resort terrace"></div>
      <div class="tile doctors" role="img" aria-label="Team of medical staff in white coats"></div>
      <div class="tile membership" role="img" aria-label="Membership terms document with a pen"></div>
    </div>
  </main>

  <footer class="site-footer">
    <div class="social"><span></span><span></span><span></span></div>
    <p class="copyright">Copyright ©2010 Veloria. All Rights Reserved</p>
    <div class="footer-brand"><span class="brand-mark"></span><span class="brand-name">Veloria</span></div>
  </footer>
</div>
</body>
</html>
```